Zolvana Stationary and Branding Documents

Corporate Identity Branding stationary needed for IT Recruiting Firm.

I already have a Logo, business cards and website. I need to get designs completed for the remaining corporate identity documents.

The documentation should use similar colors as my website and business card. The designs should modern and clean.

http://zolvanaworks.example/

Target Market(s)

Information Technology Industry

Industry/Entity Type

Information Technology

Colors
3377b5
0255a3
fbee3e
f78f20
f37122
33a6d7
000000
0592cd

Requirements
Must have
• Letter Head
• Folder Design
• PowerPoint Design
• Invoice
• Envelope
Nice to have
• Proposal
• Flyer
• Brochure
Should not have
• Logo
• Business Cards
• Website

```html
<!DOCTYPE html>
<html lang="en">
<head>
<meta charset="utf-8">
<title>Zolvana Stationery Set</title>
<link href="https://fonts.googleapis.com/css2?family=Questrial&family=Open+Sans:wght@400;700&family=Cinzel:wght@500&display=swap" rel="stylesheet">
<style>
  :root {
    --brand-blue: #0255a3;
    --brand-blue-mid: #3377b5;
    --brand-sky: #1a7cc6;
    --brand-orange: #f37122;
    --brand-orange-soft: #f78f20;
    --ink: #333;
    --muted: #777;
    --row-grey: #ebebeb;
    --page: #ffffff;
    --backdrop: #ffffff;
  }
  * { box-sizing: border-box; margin: 0; padding: 0; }
  html, body { width: 1200px; height: 1200px; overflow: hidden; background: var(--backdrop); }
  body { position: relative; font-family: "Questrial", sans-serif; color: var(--ink); }

  .sheet { position: absolute; background: var(--page); outline: 1px solid #e2e2e2; }
  .abs { position: absolute; }

  /* brand name block */
  .brand-name { font-family: "Questrial", sans-serif; color: var(--brand-blue); line-height: 1; white-space: nowrap; display: flex; align-items: center; gap: .18em; }
  .brand-name .dot { width: .22em; height: .22em; background: var(--brand-orange); display: inline-block; }
  .brand-tag { font-family: "Questrial", sans-serif; color: var(--brand-orange); letter-spacing: .08em; white-space: nowrap; text-transform: uppercase; }

  .head-rule { position: absolute; height: 1px; background: var(--brand-blue-mid); }
  .foot-rule { position: absolute; height: 1px; background: var(--brand-orange-soft); }
  .contact { position: absolute; text-align: right; font-family: "Open Sans", sans-serif; white-space: nowrap; }
  .contact .addr { color: var(--brand-orange); font-weight: 700; }
  .contact .line { color: var(--ink); }
  .site-url { position: absolute; font-family: "Open Sans", sans-serif; font-weight: 700; color: var(--ink); white-space: nowrap; }

  /* letterhead */
  .letterhead { left: 75px; top: 33px; width: 382px; height: 539px; }

  /* invoice */
  .invoice { left: 516px; top: 33px; width: 418px; height: 541px; font-size: 5px; }
  .invoice-title { left: 38px; top: 92px; color: var(--brand-orange); font-size: 18px; }
  .invoice-meta { left: 38px; top: 113px; color: var(--muted); font-size: 6px; line-height: 9px; }
  .parties { left: 38px; top: 134px; width: 340px; height: 75px; border: 1px solid var(--brand-orange); display: flex; gap: 2px; padding: 1px; }
  .party { flex: 1; position: relative; }
  .party-head { background: var(--brand-blue); color: #fff; font-size: 8px; height: 20px; padding: 6px 6px; }
  .party-logo { position: absolute; left: 6px; top: 30px; width: 40px; height: 32px; border: 1px solid #eee; display: flex; align-items: center; justify-content: center; font-size: 7px; color: #bbb; }
  .party-logo .brand-name { font-size: 9px; }
  .party-lines { position: absolute; left: 50px; right: 2px; top: 23px; }
  .party-lines div { background: var(--row-grey); height: 8px; margin-bottom: 1.6px; font-size: 4.5px; color: var(--muted); padding: 1.5px 3px; }
  .items-label { left: 42px; top: 218px; font-size: 8px; color: var(--ink); }
  .items { left: 40px; top: 231px; width: 338px; }
  .items-row { display: grid; grid-template-columns: 45px 190px 47px 56px; height: 20px; margin-bottom: 3px; background: var(--row-grey); font-size: 5px; color: #555; align-items: center; }
  .items-row span { text-align: center; }
  .items-row span:nth-child(2) { text-align: left; padding-left: 4px; }
  .items-row span + span { border-left: 2px solid #fff; height: 100%; display: flex; align-items: center; justify-content: center; }
  .items-row span:nth-child(2) { justify-content: flex-start; }
  .items-head { background: var(--brand-orange); color: #fff; height: 19px; margin-bottom: 4px; }
  .items-head span + span { border-left: none; }
  .notes { left: 38px; top: 411px; width: 219px; height: 66px; border: 1px solid #e6e6e6; padding: 9px 6px; font-size: 6px; }
  .notes hr { border: none; border-top: 1px solid #eee; margin-top: 9px; }
  .notes-footnote { left: 42px; top: 482px; font-size: 4px; color: #555; }
  .amount { left: 272px; top: 406px; width: 106px; }
  .amount-head { background: var(--brand-blue); color: #fff; font-size: 8px; height: 20px; text-align: center; padding-top: 6px; }
  .amount-row { display: flex; justify-content: space-between; border: 1px solid #eee; border-top: none; height: 17px; align-items: center; padding: 0 10px; font-size: 5px; color: #555; }
  .amount-row.total { height: 19px; }
  .amount-row.total strong { font-weight: 400; font-size: 11px; color: var(--brand-blue); }

  /* folder */
  .folder { position: absolute; left: 73px; top: 596px; width: 436px; height: 580px; overflow: hidden; }
  .folder svg { position: absolute; inset: 0; }
  .folder-brand { position: absolute; left: 0; right: 0; top: 84px; display: flex; flex-direction: column; align-items: center; gap: 6px; }
  .folder-brand .brand-name { color: #fff; font-size: 60px; }
  .folder-brand .brand-tag { font-size: 17px; }
  .folder-slogan { position: absolute; left: 0; right: 0; bottom: 8px; text-align: center; font-family: "Cinzel", serif; font-weight: 500; font-size: 15px; color: #1d2d4d; letter-spacing: .04em; }

  /* envelope front */
  .envelope-front { left: 550px; top: 602px; width: 584px; height: 293px; }

  /* envelope back */
  .envelope-back { position: absolute; left: 551px; top: 910px; width: 586px; height: 275px; }
</style>
</head>
<body>

  <!-- Letterhead -->
  <section class="sheet letterhead" aria-label="Letterhead">
    <div class="abs" style="left:25px; top:28px;">
      <div class="brand-name" style="font-size:22px;">Zolvana<span class="dot"></span></div>
      <div class="brand-tag" style="font-size:6px; margin-top:2px; padding-left:5px;">Business Solution LLC</div>
    </div>
    <div class="head-rule" style="left:137px; width:202px; top:52px;"></div>
    <div class="contact" style="right:43px; top:43px; font-size:4.3px; line-height:7px;">
      <div class="addr">Two Harbor Plaza 410, 9th Street NE</div>
      <div class="line">&#9742; 5550148822 &#9993; info@zolvanaworks.example</div>
    </div>
    <div class="foot-rule" style="left:25px; width:314px; top:509px;"></div>
    <div class="site-url" style="left:25px; top:513px; font-size:4.3px;">www.zolvanaworks.example</div>
  </section>

  <!-- Invoice -->
  <section class="sheet invoice" aria-label="Invoice">
    <div class="abs" style="left:38px; top:33px;">
      <div class="brand-name" style="font-size:26px;">Zolvana<span class="dot"></span></div>
      <div class="brand-tag" style="font-size:7px; margin-top:2px; padding-left:6px;">Business Solution LLC</div>
    </div>
    <div class="head-rule" style="left:160px; width:218px; top:62px;"></div>
    <div class="contact" style="right:39px; top:54px; font-size:4.5px; line-height:8px;">
      <div class="addr">Two Harbor Plaza 410, 9th Street NE</div>
      <div class="line">&#9742; 5550148822 &#9993; info@zolvanaworks.example</div>
    </div>

    <div class="abs invoice-title">Invoice 0001</div>
    <div class="abs invoice-meta">01 September , 2012<br>Payment due by 25 November 2012</div>

    <div class="abs parties">
      <div class="party">
        <div class="party-head">FROM</div>
        <div class="party-logo"><span class="brand-name">Zolvana</span></div>
        <div class="party-lines"><div>Your Address</div><div>Address Line 1</div><div>Town</div><div>Region/State</div><div>Zip/Postal Code</div></div>
      </div>
      <div class="party">
        <div class="party-head">TO</div>
        <div class="party-logo">LOGO</div>
        <div class="party-lines"><div>Your Address</div><div>Address Line 1</div><div>Town</div><div>Region/State</div><div>Zip/Postal Code</div></div>
      </div>
    </div>

    <div class="abs items-label">ITEMS</div>
    <div class="abs items">
      <div class="items-row items-head"><span>Quantity</span><span>Description</span><span>Unit Price</span><span>TOTAL</span></div>
      <div class="items-row"><span>2</span><span>Donec ac erat vel neque molestie convallis.</span><span>$600</span><span>$1200</span></div>
      <div class="items-row"><span>1</span><span>Sed eget risus ac lacus tempus sollicitudin in at magna.</span><span>$300</span><span>$300</span></div>
      <div class="items-row"><span>3</span><span>Nunc auctor nisl vel lorem aliquet pellentesque.</span><span>$800</span><span>$2400</span></div>
      <div class="items-row"><span>2</span><span>Pellentesque habitant morbi.</span><span>$20</span><span>$40</span></div>
      <div class="items-row"><span>2</span><span>In hac habitasse platea dictumst, mauris at.</span><span>$2500</span><span>$5000</span></div>
      <div class="items-row"><span>1</span><span>Aenean eget enim eget augue dictum fringilla et vitae.</span><span>$100</span><span>$100</span></div>
    </div>

    <div class="abs notes">Special Notes<hr><hr></div>
    <div class="abs notes-footnote">molestie condimentum. Curabitur mi dui, faucibus sed</div>

    <div class="abs amount">
      <div class="amount-head">AMOUNT DUE</div>
      <div class="amount-row"><span>SUBTOTAL</span><span>$9,040</span></div>
      <div class="amount-row"><span>TAX</span><span>$00.00</span></div>
      <div class="amount-row"><span>SHIPPING</span><span>$00.00</span></div>
      <div class="amount-row total"><span>TOTAL</span><strong>$9,040.00</strong></div>
    </div>

    <div class="foot-rule" style="left:42px; width:336px; top:513px;"></div>
    <div class="site-url" style="left:42px; top:518px; font-size:4.5px;">www.zolvanaworks.example</div>
  </section>

  <!-- Presentation folder -->
  <section class="folder" aria-label="Presentation folder">
    <svg width="436" height="580" viewBox="0 0 436 580">
      <defs>
        <linearGradient id="folderBlue" x1="0" y1="0" x2="0" y2="1">
          <stop offset="0" stop-color="#1b7cc6"/>
          <stop offset="1" stop-color="#0b4f8f"/>
        </linearGradient>
        <linearGradient id="swoosh" x1="0" y1="0" x2="1" y2="0">
          <stop offset="0" stop-color="#e9eef3"/>
          <stop offset="1" stop-color="#b9c6d3"/>
        </linearGradient>
        <linearGradient id="photoTones" x1="0" y1="0" x2="1" y2="1">
          <stop offset="0" stop-color="#9fc7e4"/>
          <stop offset=".5" stop-color="#dfe7ee"/>
          <stop offset="1" stop-color="#6d7e92"/>
        </linearGradient>
        <linearGradient id="slogan" x1="0" y1="0" x2="0" y2="1">
          <stop offset="0" stop-color="#f3f4f5"/>
          <stop offset="1" stop-color="#cfd3d7"/>
        </linearGradient>
      </defs>
      <rect width="436" height="580" fill="url(#folderBlue)"/>
      <path d="M0,548 C120,470 250,420 330,380 C390,345 420,300 436,232 L436,548 Z" fill="url(#swoosh)"/>
      <path d="M0,548 C80,480 190,400 300,378 C360,365 400,352 436,344 L436,542 L0,542 Z" fill="url(#photoTones)" role="img" aria-label="Photo of three smiling business colleagues reviewing work together in a bright office"/>
      <rect y="542" width="436" height="38" fill="url(#slogan)"/>
    </svg>
    <div class="folder-brand">
      <div class="brand-name">Zolvana<span class="dot"></span></div>
      <div class="brand-tag">Business Solution LLC</div>
    </div>
    <div class="folder-slogan">JOIN THE ELITE</div>
  </section>

  <!-- Envelope front -->
  <section class="sheet envelope-front" aria-label="Envelope front">
    <div class="abs" style="left:27px; top:30px;">
      <div class="brand-name" style="font-size:36px;">Zolvana<span class="dot"></span></div>
      <div class="brand-tag" style="font-size:10px; margin-top:3px; padding-left:10px;">Business Solution LLC</div>
    </div>
    <div class="head-rule" style="left:192px; width:368px; top:66px;"></div>
    <div class="contact" style="right:32px; top:54px; font-size:6.5px; line-height:11px;">
      <div class="addr">Two Harbor Plaza 410, 9th Street NE</div>
      <div class="line">&#9742; 5550148822 &#9993; info@zolvanaworks.example</div>
    </div>
    <div class="foot-rule" style="left:18px; width:540px; top:267px;"></div>
    <div class="site-url" style="left:18px; top:273px; font-size:6.5px;">www.zolvanaworks.example</div>
  </section>

  <!-- Envelope back -->
  <section class="envelope-back" aria-label="Envelope back">
    <svg width="586" height="275" viewBox="0 0 586 275">
      <rect width="586" height="275" fill="#0359a7"/>
      <path d="M10,0 L42,124 Q46,138 62,138 L524,138 Q540,138 544,124 L576,0" fill="none" stroke="#024a8d" stroke-width="1.5"/>
      <path d="M0,8 L30,160 M586,8 L556,160" stroke="#024a8d" stroke-width="1" opacity=".6"/>
    </svg>
  </section>

</body>
</html>
```